Wealth Education Business Needs Sharp Business Card Design

We need a business card design for a recently launched investor education business called Harbor Crest.

The final design should promote security, empowerment, self improvement and financial gain. The card will ideally promote the stature of the business.

For more information and colours please visit harborcrest.com.au

Target Market(s)

Corporate executives and high net worth individuals

Industry/Entity Type

Education

Contact Information for Business Card

```html
<!DOCTYPE html>
<html lang="en">
<head>
<meta charset="utf-8">
<title>Harbor Crest — Business Card</title>
<link href="https://fonts.googleapis.com/css2?family=Oswald:wght@500;600&family=Open+Sans:wght@400;600&display=swap" rel="stylesheet">
<style>
  :root {
    --backdrop: #e9eaec;
    --navy-deep: #0a111a;
    --navy: #1b2b3c;
    --navy-glow: #2a4158;
    --notch: #0e1722;
    --panel-light: #f4f4f4;
    --panel-mid: #d9d9d9;
    --band: #0b0d10;
    --teal: #2a9fa8;
    --slate: #8f959b;
    --ink: #1f2124;
    --white: #ffffff;
  }
  * { margin: 0; padding: 0; box-sizing: border-box; }
  html, body { width: 1200px; height: 900px; overflow: hidden; }
  body {
    background: var(--backdrop);
    font-family: "Open Sans", Arial, sans-serif;
    position: relative;
  }
  .card {
    position: absolute;
    top: 120px;
    width: 400px;
    height: 660px;
    border-radius: 24px;
    overflow: hidden;
    box-shadow: 0 14px 36px rgba(0,0,0,0.28);
  }
  .card--front { left: 170px; background: var(--panel-light); }
  .card--back {
    left: 630px;
    background: radial-gradient(ellipse at 45% 45%, var(--navy-glow) 0%, var(--navy) 35%, var(--navy-deep) 80%);
  }

  /* Front */
  .front__header {
    position: absolute; left: 0; top: 0; width: 100%; height: 250px;
    background: radial-gradient(ellipse at 50% 55%, var(--navy-glow) 0%, var(--navy) 45%, var(--navy-deep) 100%);
    display: flex; align-items: center; justify-content: center;
    z-index: 1;
  }
  .brand-name {
    font-family: "Oswald", "Arial Narrow", sans-serif;
    font-weight: 600;
    color: var(--white);
    letter-spacing: 3px;
    text-transform: uppercase;
    white-space: nowrap;
  }
  .front__header .brand-name { font-size: 38px; margin-top: 24px; }
  .header-notch {
    position: absolute; left: 50%; top: 249px;
    transform: translateX(-50%);
    z-index: 2;
  }

  .front__details {
    position: absolute; left: 0; top: 250px; width: 100%; height: 330px;
    background: radial-gradient(ellipse at 50% 40%, var(--white) 0%, var(--panel-light) 45%, var(--panel-mid) 100%);
    text-align: center;
    color: var(--ink);
  }
  .holder-name {
    margin-top: 40px;
    font-family: "Oswald", "Arial Narrow", sans-serif;
    font-weight: 600;
    font-size: 40px;
    line-height: 1;
    letter-spacing: 0.5px;
  }
  .holder-name__first { color: var(--teal); }
  .holder-name__last { color: var(--slate); }
  .holder-position { font-size: 18px; margin-top: 6px; }
  .details-rule {
    width: 240px; height: 1px; margin: 14px auto 16px;
    background: linear-gradient(90deg, transparent, #9aa0a6, transparent);
  }
  .contact { font-size: 18px; line-height: 1.3; }
  .contact + .contact { margin-top: 22px; }

  .front__footer {
    position: absolute; left: 0; bottom: 0; width: 100%; height: 80px;
    background: var(--band);
    display: flex; align-items: center; justify-content: center;
    color: var(--white);
    font-size: 21px;
    letter-spacing: 0.3px;
  }

  /* Back */
  .back__brand {
    position: absolute; left: 0; top: 0; width: 100%; height: 100%;
    display: flex; flex-direction: column; align-items: center; justify-content: center;
  }
  .back__brand-row { display: flex; align-items: center; gap: 12px; }
  .brand-mark { width: 22px; height: 22px; background: var(--teal); }
  .back__brand .brand-name { font-size: 34px; }
  .tagline {
    margin-top: 4px;
    margin-left: 34px;
    font-family: "Oswald", "Arial Narrow", sans-serif;
    font-weight: 500;
    font-size: 13px;
    letter-spacing: 3px;
    color: var(--teal);
    text-transform: uppercase;
    white-space: nowrap;
  }
</style>
</head>
<body>
  <section class="card card--front" aria-label="Business card front">
    <header class="front__header">
      <span class="brand-name">Harbor Crest</span>
    </header>
    <svg class="header-notch" width="36" height="16" viewBox="0 0 36 16" aria-hidden="true">
      <polygon points="0,0 36,0 18,16" fill="var(--notch)"/>
    </svg>
    <div class="front__details">
      <h1 class="holder-name"><span class="holder-name__first">YOUR</span> <span class="holder-name__last">NAME</span></h1>
      <p class="holder-position">Position</p>
      <div class="details-rule"></div>
      <p class="contact">Level 5, 42 Quayside Walk<br>Portview VIC 3100</p>
      <p class="contact">T: 1300 555 018<br>M: +613 5550 2947</p>
      <p class="contact">E: support@harborcrest.com.au</p>
    </div>
    <footer class="front__footer">www.harborcrest.com.au</footer>
  </section>

  <section class="card card--back" aria-label="Business card back">
    <div class="back__brand">
      <div class="back__brand-row">
        <span class="brand-mark" aria-hidden="true"></span>
        <span class="brand-name">Harbor Crest</span>
      </div>
      <span class="tagline">Study Build Thrive</span>
    </div>
  </section>
</body>
</html>
```